Residential Mortgage Leader needs Wordpress Design

Looking for a home page website design for a client. We develop using the WordPress platform and would prefer the design be at least loosely based on an existing WordPress template. Attached files have many notes from our creative brief with client. The site must be responsive. Approved, basic wireframe attached. There is room for interpretation.

Existing web site: http://www.marisolkettering.example/

The Marisol Kettering Team relies on strong systems to deliver an on-time, done-right, friendly experience. Marisol offers mortgages and refinancing services throughout the United States. She is a successful Brookvale Funding agent who strives to be an active part of her community. She would like to focus the site on her team, rather than just her.

Difference makers...
When you work with the Marisol Kettering team you get a high level of expertise and a friendly experience.

She has amazing credentials. Marisol is widely recognized as a top producer for her company, and has earned a number of awards and honors for her customer service.

Marisol's team is very engaged and enjoys sharing social comments or photos from their community.

Imagery:
* Friendly, warm imagery, preferably of her team or an image to represent her team
* Clean and crisp
* Professional / Experts in mortgage and refinance
* Clean / Good use of white space
Updates

When possible, please use imagery from the DFW area. The client mentioned they would prefer not to see stock images. Thanks.

Amend that- creative use of stock images, however, is fine. A few designs have used stock imagery, but in a well-considered manner.

We added some photos and graphics that are local. We are Dallas / Ft. Worth, Plano, Frisco, Texas. We also added some examples of photos to use for the "In the Community" area. Stock photos of business folks just doesn't fit there. Thanks!

Target Market(s)

They service a lot of builders, but also work with homeowners. Their typical client is usually a woman searching for mortgage services online. She typically has a family and may refer her husband to Marisol's team. Keep in mind, however, they also see a number of other scenarios. Most of their clients are middle to high-end borrowers.

Industry/Entity Type

It Company

Requirements
Must have
• Design should be developed using program such as Photoshop or Fireworks or Illustrator as last preference. Ideally, the design would be based on an existing responsive WordPress theme, which we would customize. You must include the name of the target theme. The footer should include lots of space for disclaimers and legal language. Site navigation should include these choices: "Home, About, Builders, Mortgage Info, Approval, Blog, Contact"
Nice to have
• Blog, social media and photos area. Use of the already approved style prototype with colors and fonts (Lato- a Google font, Times New Roman and Cookie-a decorative Google font). However, we are open to interpretation.
Should not have
• Hard to read fonts or a lack of white space.

```html
<!DOCTYPE html>
<html lang="en">
<head>
<meta charset="utf-8">
<title>Brookvale Funding – Marisol Kettering Team</title>
<link href="https://fonts.googleapis.com/css2?family=Lato:wght@300;400;700&display=swap" rel="stylesheet">
<style>
:root{
  --red:#b3160d;
  --red-dark:#8e0f08;
  --ink:#333;
  --muted:#777;
  --panel:#f6f6f6;
  --band:#efefef;
  --footer:#232323;
  --footer-line:#3c3c3c;
  --footer-text:#cfcfcf;
  --blue:#2a9fd8;
}
*{box-sizing:border-box;margin:0;padding:0}
html,body{width:972px;height:1200px;overflow:hidden}
body{position:relative;font-family:'Lato',sans-serif;color:var(--ink);background:#fff}
.abs{position:absolute}
.topbar{left:0;top:0;width:972px;height:4px;background:#333}
.header{left:0;top:4px;width:972px;height:101px;background:#f7f7f7}
.support{left:721px;top:2px;width:162px;height:24px;background:#2b2b2b;border-radius:0 0 3px 3px;color:#fff;font-size:12px;font-weight:700;line-height:24px;text-align:center}
.support em{font-style:normal;color:#9fd33a;font-size:14px;margin-left:4px}
.brand{left:105px;top:42px}
.brand-name{font-size:28px;font-weight:700;color:var(--red);letter-spacing:-0.5px;display:flex;align-items:center;gap:10px}
.brand-name i{display:inline-block;width:22px;height:22px;border-radius:50%;background:var(--red)}
.brand-sub{font-size:12px;font-weight:700;color:#444;margin-top:2px}
.follow{left:726px;top:69px;font-size:10px;font-weight:700;letter-spacing:.5px;color:#222;display:flex;align-items:center;gap:5px}
.follow span{margin-right:14px}
.follow i{display:inline-block;width:17px;height:17px;border-radius:2px}
.nav{left:0;top:105px;width:972px;height:33px;background:linear-gradient(#c8231a,#9c1209);border-top:1px solid #d43a30}
.nav a{position:absolute;top:0;line-height:33px;color:#fff;font-size:12px;text-decoration:none;transform:translateX(-50%)}
.nav a.active{left:105px;transform:none;top:5px;line-height:23px;height:23px;padding:0 8px;background:#2a2a2a;border-radius:2px}
.nav .sep{position:absolute;top:0;width:1px;height:33px;background:#7e0c06;box-shadow:1px 0 0 #d2463c}
.hero{left:0;top:138px;width:972px;height:366px;background:linear-gradient(100deg,#6f7d4e 0%,#b8a88c 30%,#d8d2c6 48%,#a9876d 65%,#7c5b48 82%,#5c6a3c 100%)}
.hero-card{left:98px;top:231px;width:357px;height:163px;background:rgba(30,30,30,.9);border-top:3px solid #111;color:#fff;padding:12px 13px}
.hero-card h1{font-weight:400;font-size:36px;letter-spacing:-1px;line-height:1.1}
.hero-card p{font-size:14px;font-weight:300;line-height:18px;margin-top:12px;letter-spacing:-.2px}
.hero-actions{display:flex;align-items:center;gap:9px;margin-top:16px;font-size:12px}
.btn{display:inline-block;height:30px;line-height:30px;padding:0 15px;font-size:12px}
.btn-red{background:var(--red);color:#fff}
.btn-white{background:#fff;color:#222;font-weight:700}
.dots{left:808px;top:434px;display:flex;gap:6px}
.dots i{width:8px;height:8px;border-radius:50%;background:#444}
.dots i:first-child{background:var(--red)}
.band{left:0;top:504px;width:972px;height:121px;background:var(--band);border-bottom:1px solid #f0cfcf}
.creds{left:89px;top:453px;width:794px;height:179px;background:var(--panel);box-shadow:0 0 8px rgba(0,0,0,.08)}
.col{position:absolute;top:0;height:179px}
.col+.col{border-left:1px solid #e4e4e4}
.col h2{font-weight:400;font-size:16px;text-align:center;margin-top:22px;color:#222}
.cred-title{font-size:23px!important;text-align:left!important;margin:18px 0 0 21px!important;letter-spacing:-.5px}
.cred-title b{font-weight:700}
.cred-mark{left:14px;top:62px;width:60px;height:46px;border-radius:50%;background:var(--red)}
.cred-text{left:107px;top:58px;width:140px;font-size:10px;line-height:14.5px;color:var(--muted);font-weight:300}
.cred-text2{left:15px;top:130px;width:250px;font-size:10px;color:var(--muted);font-weight:300}
.read{left:15px;top:150px;font-size:10px;color:var(--red)}
.badge{width:64px;height:64px;border-radius:50%;background:#fff;border:2px solid #e2e2e2;margin:8px auto 0;display:flex;align-items:center;justify-content:center}
.col p{font-size:10px;line-height:13px;color:var(--muted);font-weight:300;text-align:center;margin:16px 14px 0}
.engaged{left:0;top:645px;width:972px;text-align:center;color:var(--red);font-size:21px;letter-spacing:-.3px}
.sect{font-size:16px;font-weight:400;color:#222;padding-bottom:6px;border-bottom:1px solid #ececec}
.blog{left:107px;top:694px;width:220px}
.blog ul{list-style:none;margin-top:14px}
.blog li{font-size:11px;height:25px;padding-left:14px;position:relative;color:#333}
.blog li::before{content:"";position:absolute;left:0;top:4px;border-left:5px solid #333;border-top:3px solid transparent;border-bottom:3px solid transparent}
.social{left:356px;top:694px;width:210px}
.post{position:absolute;left:0;width:210px;display:flex;gap:11px}
.post i{flex:none;width:32px;height:32px;border-radius:2px}
.post p{font-size:10px;line-height:13.5px;color:#555;font-weight:300}
.post p b{font-weight:400;font-size:10.5px;margin-right:8px}
.community{left:651px;top:694px;width:205px}
.thumb{position:absolute;width:95px;height:73px}
.footer{left:0;top:919px;width:972px;height:281px;background:var(--footer);border-top:4px solid #4a4a4a}
.fh{position:absolute;top:29px;font-size:13px;color:#fff}
.fline{left:107px;top:52px;width:776px;height:1px;background:var(--footer-line)}
.ftext{position:absolute;font-size:10px;line-height:14.5px;color:var(--footer-text);font-weight:300}
.ftext em{font-style:normal;color:#e3342a}
.cta{left:109px;top:158px;height:25px;width:207px;background:var(--red);color:#fff;font-size:10.5px;line-height:25px;text-align:center;border:1px solid #d0392f}
.select{left:374px;top:158px;width:182px;height:26px;background:#4a4a4a;color:#ddd;font-size:10.5px;font-style:italic;line-height:26px;padding-left:9px}
.select::after{content:"";position:absolute;right:9px;top:10px;border-top:6px solid #bbb;border-left:4px solid transparent;border-right:4px solid transparent}
.portrait{left:616px;top:76px;width:96px;height:102px;border:3px solid #555;background:linear-gradient(160deg,#7a5a46,#c79a7c 55%,#4a3a33)}
.role{left:731px;top:81px;font-size:13px;color:#fff;font-weight:300}
.contact{left:732px;top:108px;font-size:10.5px;line-height:16.3px;color:#9a9a9a}
.fbot{left:107px;top:233px;width:776px;height:1px;background:var(--footer-line)}
.legal{left:107px;top:251px;font-size:10.5px;color:#8a8a8a}
.eho{left:847px;top:244px;width:30px;height:30px}
</style>
</head>
<body>
<div class="abs header"></div>
<div class="abs topbar"></div>
<div class="abs support">24/7 Live Support <em>Online</em></div>

<div class="abs brand">
  <div class="brand-name">Brookvale Funding <i></i></div>
  <div class="brand-sub">A Redmill Capital Company</div>
</div>

<div class="abs follow"><span>FOLLOW US</span>
  <i style="background:#5cb8e6"></i><i style="background:#555"></i><i style="background:#c4302b"></i><i style="background:#eee;border:1px solid #ddd"></i>
</div>

<nav class="abs nav">
  <a class="active" href="#">Home</a>
  <span class="sep" style="left:186px"></span>
  <a href="#" style="left:240px">About Us</a>
  <span class="sep" style="left:298px"></span>
  <a href="#" style="left:360px">Builders</a>
  <span class="sep" style="left:415px"></span>
  <a href="#" style="left:488px">Mortage Info</a>
  <span class="sep" style="left:555px"></span>
  <a href="#" style="left:616px">Approval</a>
  <span class="sep" style="left:671px"></span>
  <a href="#" style="left:724px">Blog</a>
  <span class="sep" style="left:771px"></span>
  <a href="#" style="left:836px">Contact Us</a>
</nav>

<div class="abs hero" role="img" aria-label="Smiling family of five in front of a suburban house with a sold sign on the lawn"></div>
<div class="abs hero-card">
  <h1>Earning Your Business</h1>
  <p>The Marisol Kettering Team relies on strong systems<br>to deliver on-time, done-right and friendly eperience</p>
  <div class="hero-actions"><span class="btn btn-red">Start Here</span> Or <span class="btn btn-white">Get to know us</span></div>
</div>
<div class="abs dots"><i></i><i></i><i></i><i></i></div>

<div class="abs band"></div>
<section class="abs creds">
  <div class="col" style="left:0;width:265px">
    <h2 class="cred-title">Our <b>Credentials</b></h2>
    <div class="abs cred-mark"></div>
    <div class="abs cred-text">Lorem Ipsum is simply dummy text of the printing and type-setting industry. Lorem Ipsum has been the industry's stand-ard dummy text is the lorem</div>
    <div class="abs cred-text2">text ever since the 1500s, when an unknown printer</div>
    <div class="abs read">[ Read More. . . ]</div>
  </div>
  <div class="col" style="left:265px;width:264px">
    <h2>Awards</h2>
    <div class="badge"><svg width="38" height="30" viewBox="0 0 38 30"><circle cx="19" cy="9" r="7" fill="#333"/><circle cx="9" cy="19" r="7" fill="#333"/><circle cx="29" cy="19" r="7" fill="#333"/><circle cx="19" cy="22" r="7" fill="#333"/></svg></div>
    <p>Lorem Ipsum is simply dummy text of the printing and typesetting industry. Lorem Ipsum has been the industry's standardLorem Ipsum.</p>
  </div>
  <div class="col" style="left:529px;width:265px">
    <h2>Recognition</h2>
    <div class="badge"><svg width="30" height="46" viewBox="0 0 30 46"><circle cx="15" cy="14" r="12" fill="#222"/><path d="M10 24 L9 44 L15 38 L21 44 L20 24Z" fill="#222"/></svg></div>
    <p>Lorem Ipsum is simply dummy text of the printing and typesetting industry. Lorem Ipsum has been the industry's standardLorem Ipsum.</p>
  </div>
</section>

<h2 class="abs engaged" style="font-weight:400">Engaged in our Community</h2>

<section class="abs blog">
  <h3 class="sect">Blog</h3>
  <ul>
    <li>Borrowing</li><li>Best Practices</li><li>Announcements</li><li>Resources</li><li>How to guides</li><li>Builders info</li>
  </ul>
</section>

<section class="abs social">
  <h3 class="sect" style="width:210px">Social</h3>
  <div class="post" style="top:37px"><i style="background:#2a9fd8"></i><p><b style="color:var(--blue)">@jordyn_vale</b>Lorem Ipsum is simply dummy text of the printing and typesetting industry.</p></div>
  <div class="post" style="top:92px"><i style="background:#3b5998"></i><p><b style="color:#3b5998">Evan Torres</b>Lorem Ipsum is simply dummy text of the printing and typesetting industry.</p></div>
  <div class="post" style="top:148px"><i style="background:#d8412f"></i><p><b style="color:#d8412f">Dale Whitford</b>Lorem Ipsum is simply dummy text of the printing and typesetting industry.</p></div>
</section>

<section class="abs community">
  <h3 class="sect">In the Community</h3>
  <div class="thumb" style="left:0;top:37px;background:linear-gradient(135deg,#cfd6dc,#5a6672)" role="img" aria-label="Team member at a local business event"></div>
  <div class="thumb" style="left:101px;top:37px;background:linear-gradient(135deg,#eef1f4,#8d99a6)" role="img" aria-label="Team member smiling in the office"></div>
  <div class="thumb" style="left:0;top:118px;background:linear-gradient(135deg,#6b6b6b,#1e1e1e)" role="img" aria-label="Portrait of a community partner"></div>
  <div class="thumb" style="left:101px;top:118px;background:linear-gradient(135deg,#e6eef5,#6f8aa3)" role="img" aria-label="Team member by an airport window"></div>
</section>

<footer class="abs footer">
  <h4 class="fh" style="left:110px;font-weight:400">Disclaimer</h4>
  <h4 class="fh" style="left:377px;font-weight:400">Language</h4>
  <h4 class="fh" style="left:619px;font-weight:400">About Marisol Kettering</h4>
  <div class="abs fline"></div>
  <p class="ftext" style="left:110px;top:77px;width:220px"><em>Lorem Ipsum</em> is simply dummy text of the printing and typesetting industry. Lorem Ipsum has been the industry's standard dummy text ever since the 1500s, when an unknown printer took a galley of type and scrambled</p>
  <div class="abs cta">Be contacted by a customer consultant</div>
  <p class="ftext" style="left:374px;top:75px;width:190px;letter-spacing:-.3px">Lorem Ipsum is simply dummy text of the printing and typesetting industry. Lorem Ipsum has been the industry's standard dummy text ever since the 1500s</p>
  <div class="abs select">English</div>
  <div class="abs portrait" role="img" aria-label="Portrait of Marisol Kettering, branch manager"></div>
  <div class="abs role">Branch Manager</div>
  <div class="abs contact">Office: 555.010.2200<br>Cell: 555.010.8830<br>mkettering@brookvalefunding.example<br>NMLS: 4021<br>410 Larkfield Square, Ste.120<br>Larkfield, TX 75500<br>Directions</div>
  <div class="abs fbot"></div>
  <div class="abs legal">Marisol Kettering • Legal</div>
  <svg class="abs eho" viewBox="0 0 30 30"><rect x="3" y="6" width="24" height="20" fill="none" stroke="#777" stroke-width="2"/></svg>
</footer>
</body>
</html>
```